Web Developer Needs a Business Card Design

I need a personal business card design that represents me as a web developer for potential employers. I would like the background to be a dark color on the front for contrast with my logo and name. The back will have all my information along with a smaller version of the logo. I want something with a modern look and feel, not too conservative. This will be used for potential employers and freelance work.

Industry/Entity Type

Business

Contact Information for Business Card

Front should have my logo and name. The back should have all my personal information which would include: name: Tom Varulek, phone: 570-614-3098, email: tomvarulek@quillbox.net, website url: www.tomvarulek.net, logo, web developer.

Font styles to use
Sans Serif

Requirements
Must have
• Must include my logo. The color palette base color will be the logo color.

```html
<!DOCTYPE html>
<html lang="en">
<head>
<meta charset="utf-8">
<title>Tom Varulek – Business Card</title>
<link rel="stylesheet" href="https://fonts.googleapis.com/css2?family=Open+Sans:ital,wght@0,400;0,600;1,700&display=swap">
<style>
  :root {
    --stage: #141414;
    --card: #0a0a0a;
    --card-edge: #1f1f1f;
    --accent: #86d2c4;
    --text-light: #f2f2f2;
    --text-muted: #d8d8d8;
  }
  * { box-sizing: border-box; margin: 0; padding: 0; }
  html, body {
    width: 1200px;
    height: 864px;
    overflow: hidden;
    background: var(--stage);
    font-family: "Open Sans", Arial, sans-serif;
  }
  .canvas { position: relative; width: 1200px; height: 864px; }

  .card {
    position: absolute;
    width: 540px;
    height: 309px;
    background: linear-gradient(135deg, #1a1a1a 0%, var(--card) 55%, #050505 100%);
    border: 1px solid var(--card-edge);
    box-shadow: 0 18px 40px rgba(0,0,0,0.6);
  }

  /* Front face */
  .card-front { left: 580px; top: 90px; }
  .front-mark {
    position: absolute;
    left: 50%;
    top: 72px;
    transform: translateX(-50%);
    width: 74px;
    height: 74px;
    border-radius: 50%;
    border: 9px solid var(--accent);
  }
  .front-name {
    position: absolute;
    left: 0;
    right: 0;
    top: 166px;
    text-align: center;
    color: var(--text-light);
    font-size: 27px;
    font-weight: 400;
    letter-spacing: 1px;
  }

  /* Back face */
  .card-back { left: 110px; top: 440px; }
  .back-mark {
    position: absolute;
    right: 44px;
    top: 44px;
    width: 118px;
    height: 118px;
    border-radius: 50%;
    border: 11px solid var(--accent);
    display: flex;
    align-items: center;
    justify-content: center;
  }
  .back-mark-name {
    color: var(--accent);
    font-size: 13px;
    font-weight: 600;
    text-align: center;
    line-height: 1.2;
  }
  .holder {
    position: absolute;
    left: 34px;
    top: 150px;
  }
  .holder-name {
    color: var(--accent);
    font-size: 19px;
    font-weight: 700;
    font-style: italic;
  }
  .holder-role {
    color: var(--text-muted);
    font-size: 14px;
    font-style: italic;
    margin-top: -2px;
  }
  .divider {
    position: absolute;
    left: 140px;
    right: 30px;
    top: 196px;
    height: 1px;
    background: var(--accent);
  }
  .contacts {
    position: absolute;
    left: 24px;
    top: 212px;
    list-style: none;
  }
  .contact {
    display: flex;
    align-items: center;
    gap: 10px;
    height: 23px;
    color: var(--text-muted);
    font-size: 14px;
  }
  .contact-icon {
    width: 16px;
    height: 16px;
    border-radius: 3px;
    background: var(--accent);
    display: flex;
    align-items: center;
    justify-content: center;
  }
  .contact-icon svg { width: 11px; height: 11px; }
</style>
</head>
<body>
<main class="canvas">

  <section class="card card-front" aria-label="Card front">
    <div class="front-mark"></div>
    <p class="front-name">TOM VARULEK</p>
  </section>

  <section class="card card-back" aria-label="Card back">
    <div class="back-mark"><span class="back-mark-name">Tom<br>Varulek</span></div>

    <div class="holder">
      <p class="holder-name">Lena Marsh</p>
      <p class="holder-role">Web Developer</p>
    </div>
    <div class="divider"></div>

    <ul class="contacts">
      <li class="contact">
        <span class="contact-icon">
          <svg viewBox="0 0 12 12"><path d="M2.5 1h2l1 2.5-1.3 1a6 6 0 0 0 3.3 3.3l1-1.3L11 7.5v2A1.5 1.5 0 0 1 9.5 11 8.5 8.5 0 0 1 1 2.5 1.5 1.5 0 0 1 2.5 1z" fill="#0a0a0a"/></svg>
        </span>
        (570) 614-3098
      </li>
      <li class="contact">
        <span class="contact-icon">
          <svg viewBox="0 0 12 12"><rect x="1" y="2.5" width="10" height="7" fill="none" stroke="#0a0a0a" stroke-width="1.3"/><path d="M1 2.5l5 4 5-4" fill="none" stroke="#0a0a0a" stroke-width="1.3"/></svg>
        </span>
        tomvarulek@quillbox.net
      </li>
      <li class="contact">
        <span class="contact-icon">
          <svg viewBox="0 0 12 12"><circle cx="6" cy="6" r="4.7" fill="none" stroke="#0a0a0a" stroke-width="1.2"/><ellipse cx="6" cy="6" rx="2" ry="4.7" fill="none" stroke="#0a0a0a" stroke-width="1"/><path d="M1.3 6h9.4" stroke="#0a0a0a" stroke-width="1"/></svg>
        </span>
        www.tomvarulek.net
      </li>
    </ul>
  </section>

</main>
</body>
</html>
```